Stationery Design Project

Hi All,

We need you to design stationary for a new Business and Accounting Advisory Firm. We have already got the logo designed and it is attached. If you could also if possible, match the fonts in your design to that on the logo’s provided.

What we need:
- Business Card
- A4 Letter head
- A4 Folders
- PPT template (Title page and regular page)

And what ever else you want to throw in.

We are in the process of getting the web site designed, however below is a list of websites which we like which will give you an understanding of the style that we are going for.

- plivant.example
- moldrabay.example
- tarvenhook.example
- quillorbank.example

I look forward to your seeing your design.
Updates

Hi All,

I have just realised that I forgot that i need to include a Sworn Ledgerkeepers image on the letter head, please find attaced as File 1. Could you please have this image in the bottom left header.

Regards,

Marcus

Industry/Entity Type

Business

Requirements
Must have
• Outputs:
- Documents ready to print
- Generic editable information
- Pdf copies of the documents
- Word version of letterhead

```html
<!DOCTYPE html>
<html lang="en">
<head>
<meta charset="utf-8">
<title>Brennock Partners – Business Card</title>
<link rel="stylesheet" href="https://fonts.googleapis.com/css2?family=Gelasio:wght@700&family=Open+Sans:wght@300;400;700&display=swap">
<style>
  :root {
    --bg: #e9e6e1;
    --blue-deep: #34509f;
    --blue-mid: #3f7fc2;
    --blue-cyan: #3db6d8;
    --navy-text: #2d4796;
    --orange: #f39a1e;
    --white: #ffffff;
    --serif: "Gelasio", Georgia, serif;
    --sans: "Open Sans", Arial, sans-serif;
  }
  * { box-sizing: border-box; margin: 0; padding: 0; }
  html, body { width: 1200px; height: 900px; overflow: hidden; }
  body {
    background: var(--bg);
    position: relative;
    font-family: var(--sans);
  }
  .card {
    position: absolute;
    left: 260px;
    width: 680px;
    height: 388px;
    border-radius: 3px;
    overflow: hidden;
    box-shadow: 0 10px 28px rgba(0,0,0,0.22);
  }
  .card--front {
    top: 40px;
    background: linear-gradient(120deg, var(--blue-deep) 0%, var(--blue-mid) 45%, var(--blue-cyan) 100%);
  }
  .card--back {
    top: 468px;
    background: var(--white);
  }

  /* front */
  .front-brand {
    position: absolute;
    left: 0; right: 0; top: 150px;
    text-align: center;
    color: var(--white);
  }
  .front-brand__name {
    font-family: var(--serif);
    font-weight: 700;
    font-size: 46px;
    line-height: 1;
  }
  .front-brand__tagline {
    margin-top: 8px;
    font-weight: 300;
    font-size: 17px;
    letter-spacing: 7px;
  }

  /* back */
  .back-header {
    position: absolute;
    left: 36px; top: 40px;
    color: var(--navy-text);
  }
  .back-header__name {
    font-family: var(--serif);
    font-weight: 700;
    font-size: 40px;
    line-height: 1;
  }
  .back-header__tagline {
    margin-top: 6px;
    margin-left: 4px;
    font-weight: 400;
    font-size: 14px;
    letter-spacing: 6px;
  }
  .back-panel {
    position: absolute;
    left: 0; right: 0; top: 140px; bottom: 0;
    background: linear-gradient(115deg, var(--blue-cyan) 0%, var(--blue-mid) 45%, var(--blue-deep) 100%);
  }
  .back-rule {
    position: absolute;
    left: 0; right: 0; top: 136px;
    height: 4px;
    background: var(--orange);
  }
  .back-tab {
    position: absolute;
    left: 560px; top: 139px;
  }
  .back-divider {
    position: absolute;
    left: 352px; top: 200px;
    width: 1px; height: 150px;
    background: rgba(255,255,255,0.55);
  }
  .contact-list {
    position: absolute;
    left: 36px; top: 168px;
    list-style: none;
    color: var(--white);
    font-size: 15px;
    line-height: 20px;
  }
  .contact-list li {
    display: flex;
    align-items: flex-start;
    gap: 12px;
    margin-bottom: 6px;
  }
  .contact-list svg { flex: none; margin-top: 1px; }
  .person {
    position: absolute;
    right: 90px; top: 176px;
    text-align: right;
    color: var(--white);
  }
  .person__name {
    font-weight: 700;
    font-size: 20px;
  }
  .person__role {
    font-size: 15px;
    margin-top: 2px;
  }
</style>
</head>
<body>

<section class="card card--front" aria-label="Business card front">
  <div class="front-brand">
    <div class="front-brand__name">Brennock Partners</div>
    <div class="front-brand__tagline">Business Advisors</div>
  </div>
</section>

<section class="card card--back" aria-label="Business card back">
  <div class="back-header">
    <div class="back-header__name">Brennock Partners</div>
    <div class="back-header__tagline">Business Advisors</div>
  </div>

  <div class="back-panel"></div>
  <div class="back-rule"></div>
  <svg class="back-tab" width="60" height="22" viewBox="0 0 60 22" aria-hidden="true">
    <polygon points="0,0 60,0 46,22 14,22" fill="var(--orange)"/>
  </svg>
  <div class="back-divider"></div>

  <ul class="contact-list">
    <li>
      <svg width="18" height="18" viewBox="0 0 18 18" aria-hidden="true">
        <circle cx="9" cy="9" r="9" fill="var(--orange)"/>
        <path d="M9 4a3 3 0 0 1 3 3c0 2.2-3 6-3 6s-3-3.8-3-6a3 3 0 0 1 3-3z" fill="var(--white)"/>
        <circle cx="9" cy="7" r="1.1" fill="var(--orange)"/>
      </svg>
      <span>Kade van Lindholm 15-F12<br>1234 AB, Veldmoor</span>
    </li>
    <li>
      <svg width="18" height="18" viewBox="0 0 18 18" aria-hidden="true">
        <circle cx="9" cy="9" r="9" fill="var(--orange)"/>
        <path d="M6 4.5l2 2-1 1.3c.6 1.3 1.6 2.3 2.9 2.9l1.3-1 2 2-1.3 1.6C8.6 13 5 9.4 4.7 6.1z" fill="var(--white)"/>
      </svg>
      <span>415-555-0130</span>
    </li>
    <li>
      <svg width="18" height="18" viewBox="0 0 18 18" aria-hidden="true">
        <circle cx="9" cy="9" r="9" fill="var(--orange)"/>
        <rect x="5" y="6" width="8" height="6" rx="1" fill="var(--white)"/>
        <rect x="6.5" y="4" width="5" height="2.5" fill="var(--white)"/>
      </svg>
      <span>415-555-0139</span>
    </li>
    <li>
      <svg width="18" height="18" viewBox="0 0 18 18" aria-hidden="true">
        <circle cx="9" cy="9" r="9" fill="var(--orange)"/>
        <text x="9" y="12.5" text-anchor="middle" font-family="Arial, sans-serif" font-size="11" font-weight="700" fill="var(--white)">@</text>
      </svg>
      <span>daniel@brennockpartners.example</span>
    </li>
    <li>
      <svg width="18" height="18" viewBox="0 0 18 18" aria-hidden="true">
        <circle cx="9" cy="9" r="9" fill="var(--orange)"/>
        <circle cx="9" cy="9" r="4.5" fill="none" stroke="var(--white)" stroke-width="1.2"/>
        <ellipse cx="9" cy="9" rx="2" ry="4.5" fill="none" stroke="var(--white)" stroke-width="1"/>
        <line x1="4.5" y1="9" x2="13.5" y2="9" stroke="var(--white)" stroke-width="1"/>
      </svg>
      <span>www.brennockpartners.example</span>
    </li>
  </ul>

  <div class="person">
    <div class="person__name">Daniel Orvisto</div>
    <div class="person__role">Director</div>
  </div>
</section>

</body>
</html>
```